Print and E-book Personal Injury Front and Back Book Cover

I need a book cover for a personal injury law firm book titled "Steady Ground Ahead" with the subtitle "A Practical Guide for Accident Claims." The book cover should have an image. This isas a lead generation book designed to be give to potential clients to have them sign as new clients.

Target Market(s)

Potential New Clients Looking For a Personal Injury Attorney

Industry/Entity Type

Legal

Requirements
Must have
• Title and some type of image or images

```html
<!DOCTYPE html>
<html lang="en">
<head>
<meta charset="utf-8">
<title>Steady Ground Ahead – Cover Spread</title>
<link href="https://fonts.googleapis.com/css2?family=Cinzel:wght@600;700&family=Open+Sans:wght@400&display=swap" rel="stylesheet">
<style>
  :root {
    --navy-deep: #0c2251;
    --navy: #173a78;
    --navy-light: #24508f;
    --spine: #11295a;
    --gold-light: #f6dc7a;
    --gold: #d2a229;
    --gold-dark: #8a6312;
    --body-text: #ffffff;
    --page: #ffffff;
  }
  html, body {
    margin: 0;
    padding: 0;
    width: 1200px;
    height: 386px;
    overflow: hidden;
    background: var(--page);
  }
  .canvas {
    position: relative;
    width: 1200px;
    height: 386px;
    display: flex;
    justify-content: center;
  }
  .spread {
    position: relative;
    width: 565px;
    height: 386px;
    background: radial-gradient(ellipse at 50% 45%, var(--navy-light) 0%, var(--navy) 45%, var(--navy-deep) 100%);
    overflow: hidden;
  }
  .gold {
    font-family: "Cinzel", serif;
    font-weight: 700;
    background: linear-gradient(180deg, var(--gold-light) 0%, var(--gold) 45%, var(--gold-dark) 100%);
    -webkit-background-clip: text;
    background-clip: text;
    color: transparent;
    text-shadow: 0 1px 1px rgba(0,0,0,0.25);
    margin: 0;
    line-height: 1;
    text-align: center;
  }
  .subtitle {
    font-family: "Cinzel", serif;
    font-weight: 700;
    color: var(--gold);
    text-align: center;
    margin: 0;
    white-space: nowrap;
  }

  /* Back cover */
  .back {
    position: absolute;
    left: 0; top: 0;
    width: 259px;
    height: 386px;
  }
  .back .title { position: absolute; left: 0; width: 259px; top: 24px; }
  .back .title span { display: block; }
  .back .t1 { font-size: 25px; }
  .back .t2 { font-size: 27px; margin-top: 2px; }
  .back .t3 { font-size: 21px; margin-top: 3px; }
  .back .subtitle { position: absolute; top: 103px; left: 0; width: 259px; font-size: 8.4px; }
  .blurb {
    position: absolute;
    left: 20px; top: 122px;
    width: 215px;
    font-family: "Open Sans", sans-serif;
    font-size: 6.9px;
    line-height: 10.2px;
    color: var(--body-text);
  }
  .blurb p {
    margin: 0 0 10.2px;
    text-align: justify;
    text-align-last: center;
  }

  /* Spine */
  .spine {
    position: absolute;
    left: 259px; top: 0;
    width: 48px;
    height: 386px;
    background: linear-gradient(90deg, var(--navy-deep), var(--spine) 50%, var(--navy-deep));
  }
  .spine-title, .spine-author {
    position: absolute;
    left: 50%;
    writing-mode: vertical-rl;
    transform: translateX(-50%);
    font-family: "Cinzel", serif;
    font-weight: 600;
    color: var(--gold);
    white-space: nowrap;
  }
  .spine-title { top: 22px; font-size: 14px; letter-spacing: 0.5px; }
  .spine-author { top: 279px; font-size: 11px; }

  /* Front cover */
  .front {
    position: absolute;
    left: 307px; top: 0;
    width: 258px;
    height: 386px;
  }
  .front .subtitle { position: absolute; top: 22px; left: 0; width: 258px; font-size: 8.6px; }
  .front .title { position: absolute; left: 0; width: 258px; top: 40px; }
  .front .title span { display: block; }
  .front .t1 { font-size: 38px; }
  .front .t2 { font-size: 40px; margin-top: 3px; }
  .front .t3 { font-size: 27px; margin-top: 4px; }
  .cover-photo {
    position: absolute;
    left: 10px; top: 161px;
    width: 240px; height: 180px;
    display: block;
  }
  .author {
    position: absolute;
    left: 0; width: 258px;
    top: 354px;
    font-family: "Cinzel", serif;
    font-weight: 600;
    font-size: 16px;
    color: var(--gold);
    text-align: center;
    margin: 0;
  }
</style>
</head>
<body>
<div class="canvas">
  <div class="spread">

    <section class="back">
      <h2 class="title gold">
        <span class="t1">Steady</span>
        <span class="t2">Ground</span>
        <span class="t3">Ahead</span>
      </h2>
      <p class="subtitle">A Practical Guide for Accident Claims</p>
      <div class="blurb">
        <p>Lorem ipsum dolor sit amet, consectetur adipiscing elit, sed do eiusmod tempor incididunt ut labore et dolore magna aliqua. Quis ipsum suspendisse ultrices gravida. Risus commodo viverra maecenas accumsan lacus vel facilisis. Lorem ipsum dolor sit amet, consectetur adipiscing elit, sed do eiusmod tempor incididunt ut labore et dolore magna aliqua. Quis ipsum suspendisse ultrices gravida. Risus commodo viverra maecenas accumsan lacus vel facilisis.</p>
        <p>Lorem ipsum dolor sit amet, consectetur adipiscing elit, sed do eiusmod tempor incididunt ut labore et dolore magna aliqua. Quis ipsum suspendisse ultrices gravida. Risus commodo viverra maecenas accumsan lacus vel facilisis. Lorem ipsum dolor sit amet, consectetur adipiscing elit, sed do eiusmod tempor incididunt ut labore et dolore magna aliqua. Quis ipsum suspendisse ultrices gravida. Risus commodo viverra maecenas accumsan lacus vel facilisis.</p>
        <p>Lorem ipsum dolor sit amet, consectetur adipiscing elit, sed do eiusmod tempor incididunt ut labore et dolore magna aliqua. Quis ipsum suspendisse ultrices gravida. Risus commodo viverra maecenas accumsan lacus vel facilisis. Lorem ipsum dolor sit amet, consectetur adipiscing elit, sed do eiusmod tempor incididunt ut labore et dolore magna aliqua. Quis ipsum suspendisse ultrices gravida. Risus commodo viverra maecenas accumsan lacus vel facilisis.</p>
      </div>
    </section>

    <section class="spine">
      <span class="spine-title">Steady Ground Ahead</span>
      <span class="spine-author">Author Name</span>
    </section>

    <section class="front">
      <p class="subtitle">A Practical Guide for Accident Claims</p>
      <h1 class="title gold">
        <span class="t1">Steady</span>
        <span class="t2">Ground</span>
        <span class="t3">Ahead</span>
      </h1>
      <svg class="cover-photo" viewBox="0 0 240 180" role="img" aria-label="Photo of a judge in a black robe at a courtroom bench holding a wooden gavel, with blurred figures behind">
        <defs>
          <linearGradient id="photoTone" x1="0" y1="0" x2="1" y2="1">
            <stop offset="0" stop-color="#a88358"/>
            <stop offset="0.45" stop-color="#d8cbb5"/>
            <stop offset="0.75" stop-color="#4a3b30"/>
            <stop offset="1" stop-color="#b57e43"/>
          </linearGradient>
        </defs>
        <rect width="240" height="180" fill="url(#photoTone)"/>
      </svg>
      <p class="author">Author Name</p>
    </section>

  </div>
</div>
</body>
</html>
```